Business card for my new company (Accounting firm)

I need a business card for my new business Brightwell Advisory and Ledger SA. Our services are accounting, tax, audit and financial management. Our customers are small companies, start-ups and new companies. The final design has to show financial security, trust and growth. Please find our logo attached to the business card. Text for the business card: Brightwell Advisory and Ledger SA Tomas Varenholt Director and Founder Certified Accountant Tel. 022 418 57 34 tv@clairevalconseil.ch www.clairevalconseil.ch Rue des Vergières 27 1201 Geneva
Target Market(s)
Our customers are small companies, start-ups and new companies.
Industry/Entity Type
Finance And Accounting
Contact Information for Business Card
Claireval Conseil et Comptes SA
Tomas Varenholt
Directeur et Fondateur
Expert-comptable diplômé
Tél. 022 418 57 34
tv@clairevalconseil.ch
www.clairevalconseil.ch
Rue des Vergières 27
1201 Genève

```html
<!DOCTYPE html>
<html lang="fr">
<head>
<meta charset="utf-8">
<title>Claireval Conseil et Comptes — cartes de visite</title>
<link rel="stylesheet" href="https://fonts.googleapis.com/css2?family=Saira:wght@400;500;600&display=swap">
<style>
  :root {
    --page: #e9ebee;
    --blue-deep: #1b5b8e;
    --blue-mid: #2f77ad;
    --blue-sky: #2fb0e4;
    --ink: #3b3b3d;
    --ink-soft: #58595b;
    --paper: #ffffff;
  }
  * { box-sizing: border-box; margin: 0; padding: 0; }
  html, body {
    width: 1200px; height: 1000px; overflow: hidden;
    background: var(--page);
    font-family: "Saira", sans-serif;
  }
  .card {
    position: absolute; left: 290px;
    width: 620px; height: 400px;
    border-radius: 4px; overflow: hidden;
    box-shadow: 0 6px 18px rgba(0,0,0,.12);
  }
  /* Verso */
  .card--back {
    top: 70px;
    background: linear-gradient(160deg, var(--blue-mid) 0%, var(--blue-deep) 70%);
  }
  .card--back .back-wash {
    position: absolute; left: 0; top: 40px; width: 360px; height: 360px;
    background: linear-gradient(135deg, rgba(255,255,255,.10), rgba(255,255,255,0));
  }
  .wordmark { position: absolute; right: 44px; text-align: right; font-weight: 500; }
  .wordmark__name { display: block; font-size: 64px; line-height: 1; letter-spacing: 4px; }
  .wordmark__sub { display: block; font-size: 17px; letter-spacing: 5px; margin-top: 4px; }
  .card--back .wordmark { top: 140px; color: var(--paper); }
  .card--back .wordmark__mark {
    display: block; width: 22px; height: 22px; margin: 0 0 14px auto;
    background: var(--paper); border-radius: 50%;
  }
  /* Recto */
  .card--front { top: 510px; background: var(--paper); }
  .card--front .wordmark { top: 30px; right: 40px; color: var(--ink); }
  .card--front .wordmark__name { font-size: 56px; }
  .card--front .wordmark__sub { font-size: 15px; }
  .front-band {
    position: absolute; left: 0; bottom: 0; width: 290px; height: 230px;
    background: linear-gradient(120deg, var(--blue-sky) 0%, var(--blue-mid) 60%, var(--blue-deep) 100%);
    border-top-right-radius: 24px;
  }
  .contact {
    position: absolute; right: 40px; top: 130px;
    width: 270px;
    text-align: right; color: var(--ink-soft);
    font-size: 15px; line-height: 1.35;
  }
  .contact p { white-space: nowrap; }
  .contact__name { color: var(--blue-sky); font-weight: 600; font-size: 21px; line-height: 1.2; }
  .contact__block { margin-top: 12px; }
</style>
</head>
<body>
  <section class="card card--back" aria-label="Verso de la carte">
    <div class="back-wash" role="img" aria-label="Motif décoratif bleu en filigrane"></div>
    <div class="wordmark">
      <span class="wordmark__mark"></span>
      <span class="wordmark__name">CLAIREVAL</span>
      <span class="wordmark__sub">CONSEIL ET COMPTES</span>
    </div>
  </section>

  <section class="card card--front" aria-label="Recto de la carte">
    <div class="front-band" role="img" aria-label="Grand motif décoratif en dégradé bleu"></div>
    <div class="wordmark">
      <span class="wordmark__name">CLAIREVAL</span>
      <span class="wordmark__sub">CONSEIL ET COMPTES</span>
    </div>
    <div class="contact">
      <p class="contact__name">Tomas Varenholt</p>
      <p>Directeur et Fondateur</p>
      <p>Expert-comptable diplômé</p>
      <p>Rue des Vergières 27, 1201 Genève</p>
      <div class="contact__block">
        <p>022 418 57 34</p>
        <p>tv@clairevalconseil.ch</p>
        <p>www.clairevalconseil.ch</p>
      </div>
    </div>
  </section>
</body>
</html>
```